Business Cards for a law firm

Business cards for our law firm. Use our silhoette logo and OAK PARTNERS - check our website (www.oakpartners.example)

Contact Information for Business Card

our silhouette logo, OAK PARTNERS, 800-555-0147, Dorian Pemberton, dorian@oakpartners.example

Requirements
Must have
• our silhouette logo, OAK PARTNERS, 800-555-0147, Dorian Pemberton, dorian@oakpartners.example

```html
<!DOCTYPE html>
<html lang="en">
<head>
<meta charset="utf-8">
<title>Oak Partners – Business Cards</title>
<link rel="stylesheet" href="https://fonts.googleapis.com/css2?family=Cinzel:wght@600;700&family=Arimo:wght@400&display=swap">
<style>
  :root {
    --bg: #dcdcdc;
    --card-white: #f4f4f5;
    --navy: #182f68;
    --navy-deep: #13275a;
    --ink: #1e1e22;
    --grey-band: #555555;
  }
  * { box-sizing: border-box; margin: 0; padding: 0; }
  html, body { width: 1200px; height: 1040px; overflow: hidden; }
  body { background: var(--bg); position: relative; font-family: "Arimo", Arial, sans-serif; }

  .card { position: absolute; border-radius: 16px; overflow: hidden; }

  /* Front */
  .card-front { left: 285px; top: 130px; width: 640px; height: 366px; background: var(--card-white); }
  .brand { position: absolute; display: flex; align-items: center; gap: 14px; }
  .brand-dot { border-radius: 50%; background: var(--navy); flex: none; }
  .brand-name { font-family: "Cinzel", Georgia, serif; font-weight: 700; color: var(--navy); letter-spacing: 0.08em; white-space: nowrap; }
  .card-front .brand { right: 41px; top: 44px; }
  .card-front .brand-dot { width: 36px; height: 36px; }
  .card-front .brand-name { font-size: 21px; }

  .person-name { position: absolute; left: 45px; top: 220px; font-family: "Cinzel", Georgia, serif; font-weight: 700; font-size: 21px; color: var(--navy); letter-spacing: 0.03em; }
  .rule { position: absolute; left: 45px; right: 42px; top: 255px; height: 1px; background: var(--ink); }
  .contacts { position: absolute; left: 45px; top: 267px; list-style: none; }
  .contacts li { display: flex; align-items: center; gap: 6px; height: 20px; font-size: 16px; color: var(--ink); }
  .contacts svg { width: 13px; height: 13px; fill: var(--navy); flex: none; }

  .band { position: absolute; left: 0; right: 0; bottom: 0; height: 18px; }

  /* Back */
  .card-back { left: 284px; top: 567px; width: 646px; height: 369px; background: var(--navy); }
  .card-back .brand { left: 104px; top: 150px; gap: 30px; }
  .card-back .brand-dot { width: 60px; height: 60px; background: var(--navy-deep); }
  .card-back .brand-name { font-size: 33px; color: #4a86d8; }
</style>
</head>
<body>

<section class="card card-front" aria-label="Card front">
  <div class="brand">
    <span class="brand-dot"></span>
    <span class="brand-name">OAK PARTNERS</span>
  </div>

  <h1 class="person-name">Dorian Pemberton</h1>
  <div class="rule"></div>

  <ul class="contacts">
    <li>
      <svg viewBox="0 0 16 16" aria-hidden="true"><path d="M3.2 1l2.6 0 1.2 3.4-1.7 1.3c.9 2 2.4 3.6 4.3 4.6l1.4-1.7 3.4 1.2v2.6c0 .9-.8 1.6-1.7 1.6C6.6 13.6 2.4 9.4 1.6 2.7 1.5 1.8 2.3 1 3.2 1z"/></svg>
      800-555-0147
    </li>
    <li>
      <svg viewBox="0 0 16 16" aria-hidden="true"><path d="M1 3h14v10H1z M2.3 4.2 8 8.6l5.7-4.4z" fill-rule="evenodd"/></svg>
      dorian@oakpartners.example
    </li>
    <li>
      <svg viewBox="0 0 16 16" aria-hidden="true"><circle cx="8" cy="8" r="7"/><path d="M4 5c1.5-.5 2.5.5 2.2 1.8-.3 1.2 1.4 1.3 1.2 2.8-.2 1.3-1.4 1.4-1.6 2.8C4.2 11.6 3 9.8 3 8c0-1.1.4-2.1 1-3zM9.5 3.3c1.6.6 2.8 2 3.2 3.7-1 .3-2-.4-2.2-1.3-.2-.9-1.4-1.1-1-2.4z" fill="#f4f4f5"/></svg>
      www.oakpartners.example
    </li>
  </ul>

  <svg class="band" viewBox="0 0 640 18" preserveAspectRatio="none" aria-hidden="true">
    <polygon points="0,0 415,0 411,18 0,18" fill="var(--navy)"/>
    <polygon points="421,0 640,0 640,18 417,18" fill="var(--grey-band)"/>
  </svg>
</section>

<section class="card card-back" aria-label="Card back">
  <div class="brand">
    <span class="brand-dot"></span>
    <span class="brand-name">OAK PARTNERS</span>
  </div>
</section>

</body>
</html>
```